Hartwell Estates Business Cards

I would like a business card that includes myself and my partner.
Includes: Logo, office #, email, website, our names, our numbers and possibly the address. I would also like the logo to be embossed and the card to be horizontal.
There is a photo of our yard signs to give you an idea of the colors of our business.

Target Market(s)

Everyone in real estate market.
We are in a rural area. Our clientele are from all socioeconomic backgrounds.

Industry/Entity Type

Real Estate Agent

Contact Information for Business Card

Company Name: Hartwell Estates
Our Names, Titles & Cell #'s : Dana Pembrook-Broker (555).317.6624, Marla Pembrook-Realtor (555).609.1385
Office #: (555).240.3918
Website: hartwellestates-demo.com
Joint Email: pembrook@hartwellestates-demo.com
Office Address: 418B W. Calloway Ave.
Brazoria, TX. 70913

Font styles to use
Serif

Requirements
Must have
• HORIZONTAL, Logo, Myself and my partners names, Our cell #'s, our office #, our website, our email address
Nice to have
• Embossed logo, office address, our titles.

```html
<!DOCTYPE html>
<html lang="en">
<head>
<meta charset="utf-8">
<title>Hartwell Estates Business Cards</title>
<link rel="stylesheet" href="https://fonts.googleapis.com/css2?family=Tinos:wght@400;700&display=swap">
<style>
  :root{
    --purple:#4a2266;
    --white:#ffffff;
    --ink:#3a3a3a;
    --page:#e6e3e1;
    --sky:#6aa9e0;
    --sky-light:#bcd9f2;
    --leaf:#6f9a4c;
    --pool:#2bb6d6;
    --deck:#a8774f;
  }
  *{margin:0;padding:0;box-sizing:border-box}
  html,body{width:1200px;height:1189px;overflow:hidden}
  body{background:var(--page);font-family:"Tinos",serif;position:relative}
  .card{position:absolute;left:150px;width:900px;height:514px;box-shadow:0 6px 18px rgba(0,0,0,.18);overflow:hidden}
  .card--back{top:48px;background:var(--purple)}
  .card--front{top:627px;background:var(--white)}

  /* back */
  .back-band{position:absolute;left:0;right:0;top:372px;height:64px;background:var(--white)}
  .back-web{position:absolute;left:0;right:0;top:372px;height:64px;line-height:64px;text-align:center;color:var(--purple);font-size:22px}
  .brand{position:absolute;display:flex;align-items:center;gap:18px}
  .brand__mark{border-radius:50%;flex:none}
  .brand__text{display:flex;flex-direction:column;font-weight:700;line-height:1}
  .brand__name{letter-spacing:1px}
  .brand__rule{height:2px;margin:6px 0}
  .brand__sub{align-self:flex-end;padding-right:10px}
  .card--back .brand{left:50%;top:150px;transform:translateX(-50%);color:var(--white)}
  .card--back .brand__mark{width:70px;height:70px;background:var(--white)}
  .card--back .brand__name{font-size:64px}
  .card--back .brand__rule{background:var(--white)}
  .card--back .brand__sub{font-size:38px}

  /* front */
  .art{position:absolute;inset:0}
  .card--front .brand{left:40px;top:60px;color:var(--purple);gap:14px}
  .card--front .brand__mark{width:50px;height:50px;background:var(--purple)}
  .card--front .brand__name{font-size:44px}
  .card--front .brand__rule{background:var(--purple)}
  .card--front .brand__sub{font-size:28px}
  .agent{position:absolute;color:var(--ink);white-space:nowrap}
  .agent__name{display:inline-block;background:var(--purple);color:var(--white);font-size:28px;padding:3px 14px;line-height:1.15}
  .agent__title{font-size:18px;margin:4px 0 0 50px;line-height:1.2}
  .agent__cell{font-size:20px;margin-left:82px;line-height:1.3}
  .label{color:var(--purple);font-weight:700}
  .agent--one{left:250px;top:198px}
  .agent--two{left:545px;top:198px}
  .front-web{position:absolute;right:34px;top:304px;font-size:19px;color:var(--ink);white-space:nowrap}
  .office{position:absolute;left:520px;top:340px;font-size:19px;color:var(--ink);line-height:1.4;white-space:nowrap}
</style>
</head>
<body>

<section class="card card--back" aria-label="Card back">
  <div class="brand">
    <span class="brand__mark"></span>
    <div class="brand__text">
      <span class="brand__name">HARTWELL</span>
      <span class="brand__rule"></span>
      <span class="brand__sub">Estates</span>
    </div>
  </div>
  <div class="back-band"></div>
  <div class="back-web">hartwellestates-demo.com</div>
</section>

<section class="card card--front" aria-label="Card front">
  <svg class="art" viewBox="0 0 900 514" width="900" height="514">
    <defs>
      <linearGradient id="houseTones" x1="0" y1="0" x2="0" y2="1">
        <stop offset="0" stop-color="var(--sky-light)"/>
        <stop offset=".45" stop-color="var(--sky)"/>
        <stop offset=".75" stop-color="var(--leaf)"/>
        <stop offset="1" stop-color="var(--deck)"/>
      </linearGradient>
      <linearGradient id="poolTones" x1="0" y1="0" x2="1" y2="1">
        <stop offset="0" stop-color="var(--leaf)"/>
        <stop offset=".4" stop-color="var(--sky)"/>
        <stop offset=".75" stop-color="var(--pool)"/>
        <stop offset="1" stop-color="var(--deck)"/>
      </linearGradient>
    </defs>
    <path role="img" aria-label="Photo of a coastal house with wooden deck and garden"
          d="M360,0 H900 V90 C800,150 690,185 560,185 C460,185 400,120 360,0 Z" fill="url(#houseTones)"/>
    <path class="band" d="M470,180 C620,200 780,160 900,90 V135 C780,195 640,220 500,205 Z" fill="var(--purple)"/>
    <path class="band" d="M0,345 H300 C420,345 520,390 640,514 H620 C540,420 460,380 360,372 C260,365 120,370 0,400 Z" fill="var(--purple)"/>
    <path role="img" aria-label="Photo of a backyard swimming pool beside a house"
          d="M0,514 V400 C120,370 260,365 360,372 C460,380 540,420 620,514 Z" fill="url(#poolTones)"/>
  </svg>

  <div class="brand">
    <span class="brand__mark"></span>
    <div class="brand__text">
      <span class="brand__name">HARTWELL</span>
      <span class="brand__rule"></span>
      <span class="brand__sub">Estates</span>
    </div>
  </div>

  <div class="agent agent--one">
    <span class="agent__name">Dana Pembrook</span>
    <p class="agent__title">Broker</p>
    <p class="agent__cell"><span class="label">M:</span> (555).317.6624</p>
  </div>

  <div class="agent agent--two">
    <span class="agent__name">Marla Pembrook</span>
    <p class="agent__title">Realtor</p>
    <p class="agent__cell"><span class="label">M:</span> (555).609.1385</p>
  </div>

  <p class="front-web">hartwellestates-demo.com</p>

  <div class="office">
    <p><span class="label">O:</span> (555).240.3918</p>
    <p><span class="label">E:</span> pembrook@hartwellestates-demo.com</p>
  </div>
</section>

</body>
</html>
```